Ledgerwise Forge - WordPress Theme & Logo

Design a logo and Wordpress website design for Ledgerwise Forge. Ledgerwise Forge provides cryptocurrency development services to clients who need a team to create & continue developing a new cryptocurrency or who want to replace their current cryptocurrency development team. more details in the attached document.
Updates

Target Market(s)

Entrepreneurs who are building a business / platform that makes use of an underlying cryptocurrency.

Logo Text

LF or Ledgerwise Forge

Coding

Coded - Design and coding required

Font styles to use
Sans Serif

Requirements
Must have
• Professional logo, complete coded Wordpress theme for all pages, containing all specified links and buttons
Nice to have
• It would be nice if the buttons that are meant to integrate with Dealtrail contain the necessary code for that. I can provide any necessary Dealtrail details from my account.
Should not have
• Slow loading time

```html
<!DOCTYPE html>
<html lang="en">
<head>
<meta charset="utf-8">
<title>Ledgerwise Forge</title>
<link href="https://fonts.googleapis.com/css2?family=Montserrat:wght@600;700&family=Roboto:wght@400;500;700&display=swap" rel="stylesheet">
<style>
:root{
  --navy:#0a1d58;
  --deep:#061338;
  --blue:#1c4fb5;
  --accent:#1766c8;
  --light:#e9effa;
  --ink:#222;
  --text:#555;
  --white:#fff;
  --star:#f2a81d;
}
*{box-sizing:border-box;margin:0;padding:0}
html,body{width:1200px;height:4743px;overflow:hidden}
body{font-family:'Roboto',sans-serif;color:var(--text);background:var(--white);font-size:14px;line-height:1.65}
h1,h2,h3,h4{font-family:'Montserrat',sans-serif;color:var(--ink)}
.wrap{width:980px;margin:0 auto;position:relative}
.center{text-align:center}
.rule{display:block;width:64px;height:3px;background:var(--accent);margin:14px auto 0}
.brand{display:flex;align-items:center;gap:10px;font-family:'Roboto',sans-serif;font-weight:700;font-size:14px;line-height:1.15;color:var(--navy);text-transform:uppercase}
.brand-mark{width:44px;height:44px;background:var(--blue)}
.social{display:flex;gap:6px}
.social span{width:32px;height:32px;border:1.5px solid var(--accent);border-radius:50%;display:block}
/* header */
.site-header{height:83px;border-top:4px solid var(--navy);display:flex;align-items:center}
.site-header .wrap{display:flex;align-items:center;justify-content:space-between}
.nav{display:flex;align-items:center;gap:36px;font-weight:500;font-size:14px;color:var(--ink)}
.nav .active{color:var(--accent)}
.btn-pill{background:var(--navy);color:var(--white);border-radius:30px;padding:13px 24px;font-size:12px;font-weight:500;text-transform:uppercase}
/* hero */
.hero{position:relative;height:672px;background:linear-gradient(120deg,#020a20 0%,#0b1d44 50%,#05102b 100%);overflow:hidden}
.hero-art{position:absolute;left:560px;top:60px;width:420px;height:460px;background:radial-gradient(circle,#3a3f4a 0%,#14203d 60%,transparent 75%)}
.hero-copy{position:absolute;left:110px;top:210px;color:var(--white)}
.hero-copy h1{color:var(--white);font-size:40px;line-height:1.28;font-weight:700}
.hero-copy p{font-size:22px;line-height:1.5;margin-top:10px}
.hero svg{position:absolute;left:0;bottom:0}
/* intro */
.intro{background:var(--light);height:285px;padding-top:60px}
.intro h2{font-size:27px;line-height:1.35}
.intro p{margin:28px auto 0;width:930px;font-size:14px;line-height:1.8}
/* hired */
.hired{height:690px;position:relative}
.hired-back{position:absolute;left:112px;top:382px;width:360px;height:265px;background:var(--navy)}
.hired-photo{position:absolute;left:129px;top:92px;width:360px;height:496px;background:linear-gradient(160deg,#caa27a 0%,#6d87b3 45%,#1c3160 100%)}
.hired-copy{position:absolute;left:545px;top:100px;width:545px;font-size:13px;line-height:1.85;text-align:justify}
.hired-copy h2{font-size:25px;display:flex;align-items:center;gap:20px;margin-bottom:18px}
.hired-copy h2::after{content:"";width:95px;height:3px;background:var(--accent)}
.hired-copy b{color:var(--ink)}
.ticks{list-style:none;margin:10px 0 16px}
.ticks li{position:relative;padding-left:38px;margin-bottom:8px;line-height:1.75;text-align:left}
.ticks li::before{content:"";position:absolute;left:0;top:5px;width:12px;height:12px;border:2px solid var(--accent);border-radius:50%;background:radial-gradient(circle,var(--accent) 35%,transparent 40%)}
.hired-copy p{margin-bottom:14px}
/* services */
.services{height:638px;background:linear-gradient(180deg,#0b1d5e 0%,#12308a 60%,#0d2670 100%);padding-top:60px}
.services h2{color:var(--white);font-size:32px;text-align:center}
.services .rule{background:var(--white)}
.cards{display:flex;gap:15px;margin-top:52px}
.card{width:317px;height:412px;background:var(--white);border-radius:4px;padding:26px 20px;font-size:13px;line-height:1.72}
.card-icon{width:80px;height:80px}
.card h3{font-family:'Roboto',sans-serif;font-weight:500;font-size:18px;line-height:1.4;margin:30px 0 16px}
.card .ticks li{padding-left:28px;margin-bottom:8px}
/* ceo */
.ceo{height:628px;position:relative}
.ceo-copy{position:absolute;left:110px;top:150px;width:490px;font-size:13px}
.ceo-copy h2{font-size:25px;display:flex;align-items:center;gap:14px;margin-bottom:16px}
.ceo-copy h2::after{content:"";width:60px;height:3px;background:var(--accent)}
.ceo-copy .ticks li{padding-left:36px;margin-bottom:16px;line-height:1.7;text-align:justify}
.ceo-photo{position:absolute;left:640px;top:95px;width:448px;height:448px;border-radius:50%;border:8px solid var(--navy);box-shadow:0 0 0 6px var(--white) inset}
.ceo-photo div{width:100%;height:100%;border-radius:50%;border:6px solid var(--white);background:linear-gradient(135deg,#0e1b2a 0%,#2c4b6e 45%,#8a6a4d 75%,#1b1f29 100%)}
/* testimonials */
.testimonials{height:458px;background:var(--light);padding-top:70px;position:relative}
.testimonials h2{font-size:27px}
.t-row{display:flex;gap:20px;margin-top:90px}
.t-card{width:313px;height:202px;background:var(--white);border-top:5px solid var(--blue);border-radius:8px 8px 4px 4px;box-shadow:0 3px 10px rgba(0,0,0,.12);text-align:center;padding:52px 14px 0;position:relative;font-size:13px;line-height:1.8}
.t-badge{position:absolute;top:-48px;left:50%;margin-left:-38px;width:76px;height:76px;border-radius:50%;background:var(--white);border:4px solid var(--blue);display:flex;align-items:center;justify-content:center}
.t-badge span{width:36px;height:36px;border-radius:50%;background:#9cc6e6}
.t-card h4{font-family:'Roboto',sans-serif;font-weight:500;font-size:18px;color:var(--ink)}
.t-card h4 small{font-weight:400;font-size:13px;color:var(--text)}
.stars{color:var(--star);letter-spacing:2px;font-size:12px;margin:2px 0 10px}
.arrow{position:absolute;top:264px;width:20px;height:30px}
/* talk */
.talk{height:603px;padding-top:75px}
.talk h2{font-size:27px;line-height:1.35}
.talk p.lead{width:890px;margin:40px auto 0;font-size:14px;line-height:1.85}
.steps{display:flex;justify-content:space-between;margin-top:48px;padding:0 20px}
.step{width:260px;text-align:center}
.step-icon{width:104px;height:104px;border-radius:50%;background:var(--white);box-shadow:0 6px 16px rgba(0,0,0,.15);margin:0 auto;display:flex;align-items:center;justify-content:center}
.step h3{font-family:'Roboto',sans-serif;font-weight:500;font-size:19px;margin:40px 0 12px;text-transform:uppercase}
.step p{font-size:14px;line-height:1.8}
/* cta */
.cta{height:433px;background:linear-gradient(180deg,#0b1d5e 0%,#1a43a8 100%);position:relative;padding-top:60px;color:var(--white);overflow:hidden}
.cta h2{color:var(--white);font-size:27px;line-height:1.35}
.cta p{width:890px;margin:26px auto 0;font-size:14px;line-height:1.85}
.cta .btn-light{display:inline-block;margin-top:30px;background:var(--white);color:var(--navy);font-weight:700;font-size:14px;padding:13px 30px;border-radius:30px}
.cta svg{position:absolute;left:0;bottom:0}
/* footer */
.footer{height:253px;background:#eef1f7;position:relative}
.f-cols{display:flex;padding-top:0}
.f-brand{width:270px}
.f-brand .social{margin:14px 0 0 38px}
.f-brand .social span{width:26px;height:26px;background:var(--navy);border:none}
.f-col{font-size:14px;color:var(--ink)}
.f-col h4{font-family:'Roboto',sans-serif;font-weight:500;font-size:16px;padding-bottom:4px;border-bottom:2px solid var(--navy);display:inline-block;margin-bottom:12px}
.f-col .ticks li{padding-left:32px;margin-bottom:4px;line-height:1.6}
.news{display:flex;align-items:center;justify-content:space-between;width:310px;height:48px;border:1px solid #ccd;border-radius:30px;background:var(--white);padding:0 5px 0 18px;font-size:13px;color:var(--text)}
.news span{width:40px;height:40px;border-radius:50%;background:var(--navy);display:flex;align-items:center;justify-content:center}
.copyright{position:absolute;left:110px;right:110px;bottom:0;height:50px;border-top:1px solid #ccd;text-align:center;font-size:12px;line-height:50px;color:var(--ink)}
</style>
</head>
<body>

<header class="site-header">
  <div class="wrap">
    <div class="brand"><span class="brand-mark"></span><span>Ledgerwise<br>Forge</span></div>
    <nav class="nav">
      <span class="active">HOME</span><span>BLOG</span>
      <span class="btn-pill">Schedule a Consultation</span>
      <div class="social"><span></span><span></span><span></span><span></span></div>
    </nav>
  </div>
</header>

<section class="hero">
  <div class="hero-art" role="img" aria-label="Glowing wireframe cube on a dark network background"></div>
  <div class="hero-copy">
    <h1>BUILD YOUR OWN<br>CRYPTOCURRENCY.</h1>
    <p>Secure, Easy to Use, and Managed<br>by an Expert Team</p>
  </div>
  <svg width="1200" height="150" viewBox="0 0 1200 150"><path d="M0 40 Q600 260 1200 0 V150 H0Z" fill="#1c4fb5"/><path d="M0 52 Q600 275 1200 10 V150 H0Z" fill="#e9effa"/></svg>
</section>

<section class="intro center">
  <h2>HIGH-QUALITY BLOCKCHAIN DEVELOPERS<br>ARE HARD TO FIND</h2>
  <span class="rule"></span>
  <p>You’re starting a company or running a cryptocurrency project—or both. But you don’t know what you don’t know about blockchains. So you looked for blockchain developers to design, build, launch, and support your project. It has not gone well.</p>
</section>

<section class="hired">
  <div class="hired-back"></div>
  <div class="hired-photo" role="img" aria-label="Hands typing on a laptop with blockchain network graphics overlaid"></div>
  <div class="hired-copy">
    <h2>HIRED A DEVELOPER</h2>
    <p><b>If you’ve already hired a developer</b> and are unhappy with what they’ve done so far, you’ve probably encountered one or more of these issues:</p>
    <ul class="ticks">
      <li>The developer just codes; they don’t test, write release notes, or run backend services.</li>
      <li>The developer keeps saying they need more time—and more money.</li>
      <li>The blockchain developer made promises they haven’t kept.</li>
      <li>The developer worked fast but left serious errors behind.</li>
      <li>The developer is slow to respond to user issues.</li>
    </ul>
    <p><b>If you have not hired a blockchain developer yet,</b> it’s likely because you can’t find anyone with the experience you need or at a cost you can afford. You have an aggressive delivery schedule. You want to get your product or service launched, and the blockchain development gap is holding everything back.</p>
    <p><b>We feel your pain.</b> Whether you’re deep into your own crypto project and it’s not working out, or you’re feeling the pressure to get started but don’t have the people in place you need, we can help.</p>
  </div>
</section>

<section class="services">
  <div class="wrap">
    <h2>LEDGERWISE FORGE</h2>
    <span class="rule"></span>
    <div class="cards">
      <div class="card">
        <svg class="card-icon" viewBox="0 0 80 80" fill="none" stroke="#0a1d58" stroke-width="3"><circle cx="40" cy="40" r="14"/><circle cx="40" cy="40" r="24" stroke-dasharray="6 5"/><circle cx="40" cy="8" r="5" fill="#1766c8"/><circle cx="40" cy="72" r="5" fill="#1766c8"/><circle cx="10" cy="26" r="5" fill="#1766c8"/><circle cx="70" cy="26" r="5" fill="#1766c8"/><circle cx="10" cy="54" r="5" fill="#1766c8"/><circle cx="70" cy="54" r="5" fill="#1766c8"/></svg>
        <h3>A Team of Experienced<br>Blockchain Specialists</h3>
        <ul class="ticks"><li>Our done-for-you services include everything from development and IT operations to ongoing support. You have access to a full team for less than the typical cost of a single developer. Our fixed fees provide predictability and even cover emergency troubleshooting.</li></ul>
      </div>
      <div class="card">
        <svg class="card-icon" viewBox="0 0 80 80" fill="none" stroke="#0a1d58" stroke-width="3"><circle cx="54" cy="24" r="14"/><circle cx="54" cy="24" r="6" stroke="#1766c8"/><rect x="6" y="36" width="26" height="30" rx="3"/><path d="M32 50h14l8 8-8 8H32"/></svg>
        <h3>We are your partner from<br>the very beginning</h3>
        <ul class="ticks"><li>We are your partner from the very beginning—from idea . . . to your own functioning cryptocurrency built on your own blockchain.</li></ul>
      </div>
      <div class="card">
        <svg class="card-icon" viewBox="0 0 80 80" fill="none" stroke="#0a1d58" stroke-width="3"><path d="M40 18l18 10v22L40 60 22 50V28z"/><path d="M22 28l18 10 18-10M40 38v22" stroke="#1766c8"/><circle cx="40" cy="40" r="34" stroke-dasharray="5 7"/></svg>
        <h3>What to Expect from<br>Ledgerwise Forge</h3>
        <ul class="ticks"><li>Project and team managed for you</li><li>Comprehensive support</li><li>Secure code that works</li><li>On-schedule delivery</li><li>Upfront consulting</li><li>Predictable fees</li><li>Integration help</li></ul>
      </div>
    </div>
  </div>
</section>

<section class="ceo">
  <div class="ceo-copy">
    <h2>MARCUS TELEVAN, CEO</h2>
    <ul class="ticks">
      <li>25+ years technology consulting and software development</li>
      <li>Led development for payment services startup Quillpay, which transfers billions of dollars monthly and was acquired for $663 million</li>
      <li>Consulting clients include multiple Fortune 100 financial services and technology companies, managing complex technology programs, and implementing large scale systems.</li>
      <li>Leads development of cryptocurrency projects Norvale and Brightlayer, both of which have had long successful delivery track records</li>
      <li>Successfully launched blockchain projects on time and on budget for ecommerce, social media, and technical services companies</li>
    </ul>
  </div>
  <div class="ceo-photo"><div role="img" aria-label="Portrait of the CEO working at a desk with trading charts on screen"></div></div>
</section>

<section class="testimonials">
  <div class="wrap center">
    <h2>CLIENT TESTIMONIALS</h2>
    <span class="rule"></span>
    <div class="t-row">
      <div class="t-card"><div class="t-badge"><span></span></div><h4>John Smith, <small>United States</small></h4><div class="stars">★★★★★</div><p>Lorem ipsum dolor sit amet, consectetur adip iscing elit, sed do eiusmod tempor incididu ntut labore et dolore magna.</p></div>
      <div class="t-card"><div class="t-badge"><span></span></div><h4>John Smith, <small>United States</small></h4><div class="stars">★★★★★</div><p>Lorem ipsum dolor sit amet, consectetur adip iscing elit, sed do eiusmod tempor incididu ntut labore et dolore magna.</p></div>
      <div class="t-card"><div class="t-badge"><span></span></div><h4>John Smith, <small>United States</small></h4><div class="stars">★★★★★</div><p>Lorem ipsum dolor sit amet, consectetur adip iscing elit, sed do eiusmod tempor incididu ntut labore et dolore magna.</p></div>
    </div>
  </div>
  <svg class="arrow" style="left:52px" viewBox="0 0 20 30"><path d="M16 3L5 15l11 12" fill="none" stroke="#1766c8" stroke-width="4"/></svg>
  <svg class="arrow" style="left:1128px" viewBox="0 0 20 30"><path d="M4 3l11 12-11 12" fill="none" stroke="#1766c8" stroke-width="4"/></svg>
</section>

<section class="talk center">
  <div class="wrap">
    <h2>TALK TO MARCUS ABOUT YOUR<br>BLOCKCHAIN PROJECT</h2>
    <span class="rule"></span>
    <p class="lead">Thinking out loud with someone who gets it is often the best way to move forward. Schedule a complimentary consultation with Ledgerwise Forge CEO Marcus Televan. During this free 60-minute call, you’ll discuss:</p>
    <div class="steps">
      <div class="step"><div class="step-icon"><svg width="50" height="50" viewBox="0 0 50 50" fill="none" stroke="#1766c8" stroke-width="3"><circle cx="23" cy="27" r="18"/><circle cx="23" cy="27" r="10"/><circle cx="23" cy="27" r="3" fill="#1766c8"/><path d="M23 27L44 6M38 6h6v6"/></svg></div><h3>Your Goals</h3><p>Your goals for your cryptocurrency<br>project</p></div>
      <div class="step"><div class="step-icon"><svg width="50" height="50" viewBox="0 0 50 50" fill="none" stroke="#1766c8" stroke-width="3"><circle cx="28" cy="22" r="16"/><path d="M18 32L6 44M22 22h12M28 16v12"/></svg></div><h3>Obstacles</h3><p>Any obstacles in the way of<br>those goals</p></div>
      <div class="step"><div class="step-icon"><svg width="50" height="50" viewBox="0 0 50 50" fill="none" stroke="#1766c8" stroke-width="3"><path d="M25 5a13 13 0 0 0-8 23v6h16v-6a13 13 0 0 0-8-23zM19 40h12M21 45h8"/><circle cx="25" cy="18" r="4"/></svg></div><h3>Solutions</h3><p>Potential solutions w/ timeframe<br>and cost</p></div>
    </div>
  </div>
</section>

<section class="cta center">
  <h2>FIND A TIME ON MARCUS’S CALENDAR<br>BELOW TO CHAT.</h2>
  <p>Lorem ipsum dolor sit amet, consectetur adipiscing elit, sed do eiusmod tempor incididunt ut labore et dolore magna aliqua. Ut enim ad minim veniam, quis nostrud exercitation ullamco laboris nisi ut aliquip ex ea commodo consequat.</p>
  <span class="btn-light">CALENDAR</span>
  <svg width="1200" height="110" viewBox="0 0 1200 110"><path d="M0 110 V90 Q600 -40 1200 60 V110Z" fill="#eef1f7"/></svg>
</section>

<footer class="footer">
  <div class="wrap f-cols">
    <div class="f-brand">
      <div class="brand" style="margin-left:8px"><span class="brand-mark"></span><span>Ledgerwise<br>Forge</span></div>
      <div class="social"><span></span><span></span><span></span><span></span></div>
    </div>
    <div class="f-col" style="width:170px"><h4>Quick Links</h4><ul class="ticks"><li>Home</li><li>Blog</li><li>Contact</li></ul></div>
    <div class="f-col" style="width:228px"><h4>About Links</h4><ul class="ticks"><li>Search</li><li>Privacy Policy</li><li>Terms Of Conditions</li></ul></div>
    <div class="f-col"><h4>Get Our Newsletter</h4><div class="news">Enter Email Address<span><svg width="18" height="18" viewBox="0 0 18 18"><path d="M2 9l14-7-5 14-2-5z" fill="#fff"/></svg></span></div></div>
  </div>
  <div class="copyright">© 2022 LEDGERWISE FORGE. All Rights Reserved</div>
</footer>

</body>
</html>
```